Whitcombe Business Card Design

The name of the business is Dario Whitcombe, CPA LLC
The service that we offer is Accounting, Tax & Consulting Services. I need it to have the following items:
Dario Whitcombe, Principal
Phone Number
Email Address
Physical Address

I have attached the company logo, one in black and one in white. Please provide a design in black background and the other in white background. Please include "Accounting, Tax & Consulting Services". I want the business card to be clean and very professional.

```html
<!DOCTYPE html>
<html lang="en">
<head>
<meta charset="utf-8">
<title>Dario Whitcombe, CPA LLC – Business Card</title>
<link href="https://fonts.googleapis.com/css2?family=Montserrat:wght@500;600&family=Roboto:wght@300;400&family=Roboto+Condensed:wght@700&display=swap" rel="stylesheet">
<style>
  :root {
    --page: #2b2b2b;
    --card: #efefef;
    --ink: #333536;
    --grey: #7d7f81;
    --grey-band: #8a8b8d;
    --red: #8c1418;
    --white: #ffffff;
  }
  * { margin: 0; padding: 0; box-sizing: border-box; }
  html, body { width: 1200px; height: 1138px; overflow: hidden; background: var(--page); }
  .canvas { position: relative; width: 1200px; height: 1138px; }
  .card {
    position: absolute;
    background: var(--card);
    border-radius: 16px;
    overflow: hidden;
  }
  .card--front { left: 272px; top: 184px; width: 622px; height: 376px; }
  .card--back { left: 274px; top: 606px; width: 619px; height: 375px; }

  .brand-mark { position: absolute; background: var(--ink); }
  .brand-name {
    position: absolute;
    font-family: "Montserrat", sans-serif;
    font-weight: 600;
    color: var(--ink);
    white-space: nowrap;
  }
  .brand-tagline {
    position: absolute;
    font-family: "Montserrat", sans-serif;
    font-weight: 600;
    color: var(--grey);
    letter-spacing: 2.2px;
    white-space: nowrap;
  }

  /* Front */
  .card--front .brand-mark { left: 285px; top: 96px; width: 54px; height: 54px; }
  .card--front .brand-name { left: 0; width: 100%; top: 196px; text-align: center; font-size: 25px; }
  .card--front .brand-tagline { left: 0; width: 100%; top: 233px; text-align: center; font-size: 17px; }
  .services {
    position: absolute; left: 0; width: 100%; top: 326px; text-align: center;
    font-family: "Roboto", sans-serif; font-weight: 400; font-size: 16px; color: var(--ink);
  }
  .edge-band { position: absolute; bottom: 0; height: 8px; }
  .edge-band--red { left: 0; width: 50%; background: var(--red); }
  .edge-band--grey { right: 0; width: 50%; background: var(--grey-band); }

  /* Back */
  .card--back .brand-mark { left: 28px; top: 60px; width: 52px; height: 52px; }
  .card--back .brand-name { left: 124px; top: 63px; font-size: 24px; }
  .card--back .brand-tagline { left: 124px; top: 95px; font-size: 16.5px; }
  .contact {
    position: absolute; left: 28px; top: 170px;
    font-family: "Roboto", sans-serif; font-weight: 300; font-size: 16.5px; color: var(--ink);
    list-style: none;
  }
  .contact li { display: flex; align-items: center; height: 24px; }
  .contact .address { margin-bottom: 4px; }
  .contact svg { width: 14px; height: 14px; margin-right: 13px; fill: var(--red); }
  .footer-band {
    position: absolute; left: 0; right: 0; top: 284px; bottom: 0;
    background: linear-gradient(to bottom, #9a9b9d 0%, #9a9b9d 8%, var(--red) 30%, var(--red) 100%);
  }
  .holder { position: absolute; right: 44px; top: 312px; text-align: right; color: var(--white); }
  .holder-name { font-family: "Roboto Condensed", sans-serif; font-weight: 700; font-size: 20px; line-height: 1.2; }
  .holder-role { font-family: "Roboto", sans-serif; font-weight: 300; font-size: 17px; color: #e6d3d3; line-height: 1.3; }
</style>
</head>
<body>
<main class="canvas">
  <section class="card card--front">
    <div class="brand-mark"></div>
    <p class="brand-name">DARIO WHITCOMBE, CPA, LLC</p>
    <p class="brand-tagline">CERTIFIED PUBLIC ACCOUNTANT</p>
    <p class="services">Accounting, Tax &amp; Consulting Services</p>
    <div class="edge-band edge-band--red"></div>
    <div class="edge-band edge-band--grey"></div>
  </section>

  <section class="card card--back">
    <div class="brand-mark"></div>
    <p class="brand-name">DARIO WHITCOMBE, CPA, LLC</p>
    <p class="brand-tagline">CERTIFIED PUBLIC ACCOUNTANT</p>

    <ul class="contact">
      <li class="address">1234, Anywhere Street, Town Name, US 123456</li>
      <li><svg viewBox="0 0 16 16"><path d="M1 6c0-2 3-4 7-4s7 2 7 4v1h-4V5.5H5V7H1zM4 8h8l2 6H2z"/></svg>828-555-0142</li>
      <li><svg viewBox="0 0 16 16"><path d="M1 3h14v10H1zM2 4.5v.4l6 4 6-4v-.4z"/></svg>dw@dariowhitcombellc.com</li>
      <li><svg viewBox="0 0 16 16"><path d="M8 1a7 7 0 1 0 0 14A7 7 0 0 0 8 1zm0 1.5c.8 0 1.7 1.6 2 4H6c.3-2.4 1.2-4 2-4zM2.6 7.5h2.4c0 .4 0 .7.1 1H2.6zm8.4 0h2.4v1H11zM6 9.5h4c-.3 2.4-1.2 4-2 4s-1.7-1.6-2-4z"/></svg>www.dariowhitcombellc.com</li>
    </ul>

    <div class="footer-band" role="img" aria-label="Decorative red and grey wave band along the card's lower edge"></div>

    <div class="holder">
      <p class="holder-name">DARIO WHITCOMBE</p>
      <p class="holder-role">Principal</p>
    </div>
  </section>
</main>
</body>
</html>
```